Business Cards Design for the electrical wholesaler: clean bold dynamic :)

We need a business card design that would follow our latest brand guidelines. As an electrical wholesaler we want to bring a fresh look and feel into the industry. The design should be clean bold and dynamic. It should come alive with the renewed energy of our green colour. Our grey colour should keep things balanced and complement the notion of maturity and responsibility. We employ Lato as a corporate font however are not bound by this font and we’re open to interpretation here.

Target Market(s)

Electrical contractors

Industry/Entity Type

Business

Contact Information for Business Card

Logo
Name & Surname: Halyna Dorosh
Job Title: Director of Marketing
Email: halya.dorosh@quillmail.example
Cell phone: XXX.XXX.XXXX
Address: 20517 - 87 Ave. Edmonton, AB, Canada. T6K 4N8
Business Phone: 780.555.0184
Website: www.brovix.example

Font styles to use
Other font styles liked:
• Lato

Requirements
Must have
• Logo & website
Nice to have
• Brand elements - some of them you may find in the attached Brand Guidelines (e.g. three lines on the background signifying "W")

```html
<!DOCTYPE html>
<html lang="en">
<head>
<meta charset="utf-8">
<title>Brovix Business Card</title>
<link rel="stylesheet" href="https://fonts.googleapis.com/css2?family=Lato:wght@400;700&display=swap">
<style>
  :root {
    --backdrop: #2e2e2e;
    --card: #262626;
    --green: #9ccf3c;
    --grey: #8a8a8a;
    --text: #f2f2f2;
    --divider: #6a6a6a;
  }
  * { margin: 0; padding: 0; box-sizing: border-box; }
  html, body { width: 1200px; height: 900px; overflow: hidden; }
  body {
    background: var(--backdrop);
    font-family: "Lato", sans-serif;
    display: flex;
    flex-direction: column;
    align-items: center;
    justify-content: center;
    gap: 40px;
  }
  .card {
    width: 560px;
    height: 320px;
    background: var(--card);
    position: relative;
    box-shadow: 0 10px 24px rgba(0,0,0,.35);
  }
  /* Front */
  .card-front {
    display: flex;
    flex-direction: column;
    align-items: center;
    justify-content: center;
  }
  .brand {
    display: flex;
    align-items: center;
    gap: 14px;
  }
  .brand-mark {
    width: 30px; height: 30px;
    background: var(--green);
  }
  .brand-name {
    font-size: 58px;
    font-weight: 400;
    color: var(--grey);
    line-height: 1;
  }
  .brand-tagline {
    margin-top: 8px;
    font-size: 11px;
    font-weight: 700;
    letter-spacing: 2.4px;
    color: var(--grey);
    text-transform: uppercase;
  }
  .front-website {
    margin-top: 44px;
    font-size: 13px;
    letter-spacing: 4.2px;
    color: var(--text);
  }
  /* Back */
  .identity {
    position: absolute;
    right: 310px;
    top: 92px;
    text-align: right;
  }
  .person-name {
    font-size: 27px;
    font-weight: 400;
    color: var(--green);
    line-height: 1.05;
    text-transform: uppercase;
  }
  .person-title {
    font-size: 15px;
    color: var(--text);
    text-transform: uppercase;
    margin-top: 4px;
  }
  .divider {
    position: absolute;
    left: 272px;
    top: 58px;
    width: 1px;
    height: 120px;
    background: var(--divider);
  }
  .contact-list {
    position: absolute;
    left: 292px;
    top: 66px;
    list-style: none;
  }
  .contact-list li {
    display: flex;
    align-items: center;
    gap: 9px;
    font-size: 14px;
    color: var(--text);
    height: 21px;
  }
  .contact-list svg, .address svg {
    width: 13px; height: 13px;
    fill: var(--green);
    flex: none;
  }
  .address {
    position: absolute;
    left: 40px;
    bottom: 62px;
    display: flex;
    align-items: center;
    gap: 6px;
    font-size: 15px;
    color: var(--text);
  }
</style>
</head>
<body>
  <section class="card card-front">
    <div class="brand">
      <span class="brand-mark"></span>
      <span class="brand-name">brovix</span>
    </div>
    <p class="brand-tagline">Electrical Wholesalers</p>
    <p class="front-website">www.brovix.example</p>
  </section>

  <section class="card card-back">
    <div class="identity">
      <h1 class="person-name">Halyna Dorosh</h1>
      <p class="person-title">CEO/Founder</p>
    </div>
    <span class="divider"></span>
    <ul class="contact-list">
      <li>
        <svg viewBox="0 0 16 16" aria-hidden="true"><path d="M3.5 1l2.5 3-1.5 2c1 2 3 4 5 5l2-1.5 3 2.5-1.5 2.5C8 16 0 8 1 2.5z"/></svg>
        780 555 0184
      </li>
      <li>
        <svg viewBox="0 0 16 16" aria-hidden="true"><path d="M4 0h8a1 1 0 0 1 1 1v14a1 1 0 0 1-1 1H4a1 1 0 0 1-1-1V1a1 1 0 0 1 1-1zm1 2v10h6V2zm3 11a1 1 0 1 0 0 2 1 1 0 0 0 0-2z"/></svg>
        780 555 0127
      </li>
      <li>
        <svg viewBox="0 0 16 16" aria-hidden="true"><path d="M4 1h7l1 1v3H4zM1 6h14v7h-3v2H4v-2H1zm4 5v3h6v-3z"/></svg>
        780 555 0163
      </li>
      <li>
        <svg viewBox="0 0 16 16" aria-hidden="true"><path d="M1 3h14v10H1zm1.5 1.5L8 9l5.5-4.5z"/></svg>
        halya.dorosh@quillmail.example
      </li>
      <li>
        <svg viewBox="0 0 16 16" aria-hidden="true"><path d="M8 0a8 8 0 1 0 0 16A8 8 0 0 0 8 0zm-3 4c2 0 3 1 2 3s-3 1-3 3c-1-1-2-4 1-6zm5 7c1-2 3-2 3-1-1 2-2 3-4 3z"/></svg>
        www.brovix.example
      </li>
    </ul>
    <p class="address">
      <svg viewBox="0 0 16 16" aria-hidden="true"><path d="M8 0a5.5 5.5 0 0 0-5.5 5.5C2.5 10 8 16 8 16s5.5-6 5.5-10.5A5.5 5.5 0 0 0 8 0zm0 3a2.5 2.5 0 1 1 0 5 2.5 2.5 0 0 1 0-5z"/></svg>
      20517 - 87 Ave. Edmonton, AB, Canada. T6K 4N8
    </p>
  </section>
</body>
</html>
```